Modern & Fresh Vantacor Book Cover

Need a creative e-book cover for my book.

Title: Master Vantacor Fast
Subtitle: Learn How To Easily Choose & Enroll in the Perfect Coverage at the Perfect Time.

Target Market(s)

60-70 year olds in the United States

Font styles to use
Sans Serif

Colors
9bcb3c
33a6d7

Requirements
Must have
• Must look modern and fresh.
• Use our company colors www.Movaquill.com

```html
<!DOCTYPE html>
<html lang="en">
<head>
<meta charset="utf-8">
<title>Master Vantacor Fast — Book Cover</title>
<link rel="stylesheet" href="https://fonts.googleapis.com/css2?family=League+Spartan:wght@700;800&family=Montserrat:wght@400&display=swap">
<style>
  :root {
    --stage: #e9e6df;
    --cover-paper: #ececec;
    --brand-blue: #3098c9;
    --brand-green: #8cbd36;
    --ink: #1d1d1d;
    --sky: #e4e4e2;
    --tree: #5d7a3a;
    --grass: #7fb23a;
  }
  * { margin: 0; padding: 0; box-sizing: border-box; }
  html, body {
    width: 1200px; height: 800px; overflow: hidden;
    background: var(--stage);
  }
  .cover {
    position: absolute;
    left: 350px; top: 18px;
    width: 500px; height: 764px;
    background: var(--cover-paper);
    overflow: hidden;
    box-shadow: 0 10px 30px rgba(0,0,0,0.18);
  }
  .title {
    position: absolute; left: 28px; top: 36px;
    font-family: "League Spartan", sans-serif;
    font-weight: 800;
    line-height: 1;
  }
  .title-line { display: block; white-space: nowrap; }
  .title-lead {
    color: var(--brand-blue);
    font-size: 118px;
    letter-spacing: -3px;
  }
  .title-brand {
    color: var(--brand-green);
    font-size: 88px;
    font-variant: small-caps;
    margin-top: 10px;
    letter-spacing: -1px;
  }
  .title-tail {
    color: var(--brand-blue);
    font-size: 130px;
    font-variant: small-caps;
    margin-top: -2px;
    letter-spacing: -2px;
  }
  .subtitle {
    position: absolute; left: 42px; top: 400px;
    width: 440px;
    font-family: "Montserrat", sans-serif;
    font-weight: 400;
    font-size: 22px;
    line-height: 34px;
    color: var(--ink);
    z-index: 2;
  }
  .scene {
    position: absolute; left: 0; top: 440px;
    width: 500px; height: 324px;
    background: linear-gradient(180deg,
      rgba(236,236,236,0) 0%,
      var(--sky) 18%,
      #cfd2c8 30%,
      var(--tree) 42%,
      #4d6a30 60%,
      #8a5a34 72%,
      var(--grass) 86%,
      #8fc24a 100%);
  }
</style>
</head>
<body>
  <main class="cover">
    <h1 class="title">
      <span class="title-line title-lead">Master</span>
      <span class="title-line title-brand">Vantacor</span>
      <span class="title-line title-tail">Fast</span>
    </h1>
    <p class="subtitle">Learn How To Easily Choose &amp; Enroll in the Perfect Coverage at the Perfect Time</p>
    <div class="scene" role="img" aria-label="Photo of an older couple seen from behind, sitting on a wooden park bench in front of trees and green grass"></div>
  </main>
</body>
</html>
```